New business card for a regional office of a US M&A company

We need business card for a finance company, office based in Hong Kong , our Head office is in US, our business is to Merge and acquires companies , the new office will be a regional office for the Asia Pacific region. We want to use the head office logo as attached ( but don't have to be exactly the same, can be a variation to it) as a base and then add Asia Pacific alongside the logo.
We would prefer to have be bilingual Eng + Chinese, although we don't really have Chinese company name .

Industry/Entity Type

Business

Contact Information for Business Card

Clara Jo Tsang
 

VP,
APAC M&A Operations
ORIN VANTAGE Asia Pacific Limited
 
Unit 1407, K18
18 Tai Lok Shan Road, 
Hong Kong 
 
M: +852 6038 1742
T : +852 2836 4100
F : +852 2836 4177
VOIP: 4158
 
cjtsang@orinvantage.com

Font styles to use
Serif
Sans Serif

Colors

Designer to choose colors to be used in the design.

Requirements
Must have
• APAC Office

```html
<!DOCTYPE html>
<html lang="en">
<head>
<meta charset="utf-8">
<title>Orin Vantage – APAC Business Card</title>
<link rel="stylesheet" href="https://fonts.googleapis.com/css2?family=Ubuntu:wght@400;500;700&display=swap">
<style>
  :root {
    --backdrop: #3b3c3e;
    --card-black: #161617;
    --card-charcoal: #27282b;
    --deco-grey: #2f3034;
    --emboss: #2c2c2e;
    --accent: #1aa9d6;
    --ink-light: #f2f4f5;
    --strip-grey: #e3e4e2;
  }
  * { margin: 0; padding: 0; box-sizing: border-box; }
  html, body {
    width: 799px; height: 1200px; overflow: hidden;
    background: var(--backdrop);
    font-family: "Ubuntu", sans-serif;
  }
  .card {
    position: absolute; left: 90px;
    width: 620px; height: 354px;
    overflow: hidden;
    box-shadow: 0 10px 28px rgba(0,0,0,.45);
  }
  /* front */
  .card-front { top: 140px; background: var(--card-black); }
  .front-brand {
    position: absolute; left: 0; right: 0; top: 150px;
    display: flex; align-items: center; justify-content: center; gap: 16px;
  }
  .front-brand .mark-square { width: 40px; height: 40px; background: var(--emboss); }
  .front-brand .brand-name {
    font-weight: 700; font-size: 48px; letter-spacing: 1px; color: var(--emboss);
  }
  /* back */
  .card-back { top: 706px; background: var(--card-charcoal); }
  .back-deco {
    position: absolute; left: 420px; top: 110px;
    width: 190px; height: 190px; background: var(--deco-grey);
  }
  .back-brand {
    position: absolute; left: 26px; top: 22px;
    display: flex; align-items: center; gap: 14px;
  }
  .back-brand .mark-square { width: 36px; height: 36px; background: var(--accent); }
  .back-brand .brand-name {
    font-weight: 700; font-size: 40px; letter-spacing: 1px; color: var(--accent);
  }
  .person { position: absolute; left: 28px; top: 104px; color: var(--ink-light); }
  .person-name { font-size: 20px; font-weight: 500; color: var(--accent); margin-bottom: 4px; }
  .person-title { font-size: 14px; line-height: 18px; margin-bottom: 10px; }
  .contact-line { display: flex; align-items: center; gap: 8px; font-size: 14px; line-height: 20px; }
  .contact-line svg { width: 13px; height: 13px; fill: var(--accent); flex: none; }
  .office { position: absolute; left: 330px; top: 186px; color: var(--ink-light); }
  .office-name { font-size: 15px; font-weight: 700; color: var(--accent); margin-bottom: 6px; }
  .office .contact-line { font-size: 13px; line-height: 18px; }
  .office .address { font-size: 13px; line-height: 18px; }
  .bottom-bands { position: absolute; left: 0; top: 0; width: 620px; height: 354px; }
  .website {
    position: absolute; left: 310px; top: 318px;
    font-size: 15px; letter-spacing: 1px; color: var(--ink-light);
  }
</style>
</head>
<body>

<section class="card card-front" aria-label="Card front">
  <div class="front-brand">
    <span class="mark-square"></span>
    <span class="brand-name">ORIN VANTAGE</span>
  </div>
</section>

<section class="card card-back" aria-label="Card back">
  <div class="back-deco"></div>

  <svg class="bottom-bands" viewBox="0 0 620 354" aria-hidden="true">
    <rect x="0" y="322" width="300" height="32" fill="var(--strip-grey)"/>
    <polygon points="290,298 620,298 620,354 258,354" fill="var(--accent)"/>
  </svg>

  <div class="back-brand">
    <span class="mark-square"></span>
    <span class="brand-name">ORIN VANTAGE</span>
  </div>

  <div class="person">
    <p class="person-name">Clara Jo Tsang</p>
    <p class="person-title">Vice President,<br>APAC M&amp;A Operations</p>
    <p class="contact-line">
      <svg viewBox="0 0 16 16"><rect x="4" y="1" width="8" height="14" rx="1.5"/></svg>
      +852 6038 1742
    </p>
    <p class="contact-line">
      <svg viewBox="0 0 16 16"><path d="M1 3h14v10H1z M1 3l7 6 7-6" stroke="var(--card-charcoal)" stroke-width="1"/></svg>
      cjtsang@orinvantage.com
    </p>
  </div>

  <div class="office">
    <p class="office-name">Orin Vantage Asia Pacific Limited</p>
    <p class="contact-line">
      <svg viewBox="0 0 16 16"><path d="M3 2l3 0 1 3-2 1.5c1 2 2.5 3.5 4.5 4.5L11 9l3 1v3c0 1-1 1.5-2 1.5C6 14 2 10 1.5 4 1.5 3 2 2 3 2z"/></svg>
      +852 2836 4100
    </p>
    <p class="contact-line">
      <svg viewBox="0 0 16 16"><rect x="2" y="6" width="12" height="8" rx="1"/><rect x="4" y="1" width="8" height="5"/></svg>
      +852 2836 4177,&nbsp; VOIP: 4158
    </p>
    <p class="address">Unit 1407, K18 18, Tai Lok Shan<br>Road, Hong Kong</p>
  </div>

  <p class="website">www.orinvantage.com</p>
</section>

</body>
</html>
```